R7M Horizon Business Card Design

We need a business card created for our New Business "R7M Horizon"<br/><br/>The business card design is up to you however the following information must be on the business card:<br/><br/>Front of the business card -<br/>Email :darrenp@r7mhorizon.nz<br/>Mobile: +64 (0) 22 4870 619<br/>Website: www.r7mhorizon.nz<br/>Card Owner Name: Darren Paltrow<br/>Company Title: Business Development Manager<br/>Slogan: "Two strengths, one standard". <br/>Logo On the front attached to the design brief<br/><br/>On the back: <br/>Space on the back for 4 more versions of the logo across the bottom of the card indicating different subsidiary brands - R7M Coffee, R7M Arts, R7M ?? (The card will be used for all of these brands - We Will add the extra subsidiary logos to the design once the design is finished (We are a graphics design team). <br/><br/>Other than that we want a premium feeling logo that remains universally usable depending on the business entity that we are using the card for. The use of bright bold colours would be great but we still want the card to feel premium.
Target Market(s)
Gift Design and Manufacturing Companies
Contact Information for Business Card
Front of the business card -
Email :darrenp@r7mhorizon.nz
Mobile: +64 (0) 22 4870 619
Website: www.r7mhorizon.nz
Card Owner Name: Darren Paltrow
Company Title: Business Development Manager
Slogan: "Two strengths, one standard".
Logo On the front attached to the design brief

```html
<!DOCTYPE html>
<html lang="en">
<head>
<meta charset="utf-8">
<title>R7M Horizon Business Card</title>
<link rel="stylesheet" href="https://fonts.googleapis.com/css2?family=Quicksand:wght@500;600;700&family=Open+Sans:wght@700&display=swap">
<style>
  :root {
    --bg: #2b2b2d;
    --card: #eef0f3;
    --brand-blue: #2e3a9c;
    --ink: #3a3a3d;
    --rule: #b9bcc2;
    --muted: #55575c;
  }
  * { margin: 0; padding: 0; box-sizing: border-box; }
  html, body {
    width: 1200px; height: 960px; overflow: hidden;
    background: var(--bg);
  }
  .canvas { position: relative; width: 1200px; height: 960px; }
  .card {
    position: absolute;
    width: 640px; height: 366px;
    background: var(--card);
    font-family: "Quicksand", sans-serif;
    box-shadow: 0 10px 30px rgba(0,0,0,.45);
  }
  .card--back { left: 60px; top: 70px; }
  .card--front { left: 500px; top: 500px; }

  .brand {
    color: var(--brand-blue);
    font-family: "Quicksand", sans-serif;
    font-weight: 700;
    white-space: nowrap;
  }

  .card--back .brand {
    position: absolute; left: 0; right: 0; top: 122px;
    text-align: center; font-size: 44px; line-height: 56px;
  }
  .slogan {
    position: absolute; left: 0; right: 0; top: 222px;
    text-align: center;
    font-family: "Open Sans", sans-serif; font-weight: 700;
    font-size: 12px; letter-spacing: 3px; color: var(--ink);
  }

  .card--front .brand {
    position: absolute; right: 44px; top: 48px;
    font-size: 30px; line-height: 38px;
  }
  .rule-top {
    position: absolute; left: 40px; right: 40px; top: 142px;
    border-top: 1px solid var(--rule);
  }
  .website {
    position: absolute; right: 44px; top: 160px;
    color: var(--brand-blue); font-weight: 700; font-size: 15px;
  }
  .holder { position: absolute; left: 44px; top: 214px; }
  .holder__name { color: var(--brand-blue); font-weight: 600; font-size: 22px; line-height: 1.1; }
  .holder__title { color: var(--ink); font-weight: 600; font-size: 15px; margin-top: 2px; }
  .rule-mid {
    position: absolute; left: 44px; width: 280px; top: 274px;
    border-top: 1px solid var(--rule);
  }
  .contact { position: absolute; left: 44px; top: 288px; list-style: none; }
  .contact li {
    display: flex; align-items: center; gap: 10px;
    color: var(--muted); font-weight: 600; font-size: 15px; line-height: 26px;
  }
  .contact svg { width: 14px; height: 14px; fill: none; stroke: var(--brand-blue); stroke-width: 1.8; }
</style>
</head>
<body>
<div class="canvas">
  <section class="card card--back">
    <p class="brand">R7M Horizon</p>
    <p class="slogan">TWO STRENGTHS, ONE STANDARD</p>
  </section>

  <section class="card card--front">
    <p class="brand">R7M Horizon</p>
    <div class="rule-top"></div>
    <p class="website">www.r7mhorizon.nz</p>
    <div class="holder">
      <p class="holder__name">Darren Paltrow</p>
      <p class="holder__title">Business Development Manager</p>
    </div>
    <div class="rule-mid"></div>
    <ul class="contact">
      <li>
        <svg viewBox="0 0 14 14" aria-hidden="true"><rect x="3" y="1" width="8" height="12" rx="1.5"/><line x1="6" y1="11" x2="8" y2="11"/></svg>
        +64 (0) 22 4870 619
      </li>
      <li>
        <svg viewBox="0 0 14 14" aria-hidden="true"><rect x="1" y="3" width="12" height="8"/><polyline points="1,3 7,8 13,3"/></svg>
        darrenp@r7mhorizon.nz
      </li>
    </ul>
  </section>
</div>
</body>
</html>
```